Interior Stylist business card design needed

I need a business card for my new company in Sydney called "Liv Harrowby Designs". The business offers an interior styling and colour consultancy. My clients are generally not very design savvy (hence why they use me) and can range from being quite conservative to really wanting something "out there". They can be looking for a budget makeover or something more expensive / substantial. I'd like my business card design to be stylish (but not overly formal). I certainly don't want it to be conservative. I'd like it to stand out a bit! I don't really have any aversion to particular colours and I don't have a logo as such - my business name is really all I have.

Target Market(s)

As above - home owners, ranging from conservative to modern

Industry/Entity Type

Conservative

Contact Information for Business Card

Liv Harrowby Designs
Colour consultancy and interior styling
ph: 0417 238 605
email: livharrowby@qoralnet.net.au

Requirements
Should not have
• Old fashioned writing or motifs. No Times Roman font!!

```html
<!DOCTYPE html>
<html lang="en">
<head>
<meta charset="utf-8">
<title>Liv Harrowby Designs – Business Card</title>
<link rel="stylesheet" href="https://fonts.googleapis.com/css2?family=Cormorant+Garamond:ital,wght@1,500&display=swap">
<style>
  :root {
    --backdrop: #2b1e16;
    --olive-deep: #3b3b2d;
    --olive-mid: #4a4a37;
    --olive-light: #5d5c43;
    --olive-glow: #66654a;
    --ink: #050505;
    --paper-text: #f2f0ea;
    --rule: #3a3a3a;
  }
  * { box-sizing: border-box; margin: 0; padding: 0; }
  html, body {
    width: 1200px; height: 900px; overflow: hidden;
    background: var(--backdrop);
  }
  .canvas { position: relative; width: 1200px; height: 900px; }
  .card {
    position: absolute; left: 290px;
    width: 620px; height: 354px;
    border-radius: 22px; overflow: hidden;
    box-shadow: 0 14px 30px rgba(0,0,0,.45);
  }
  .card--front { top: 70px; }
  .card--back { top: 476px; }
  .pattern-fill {
    position: absolute; inset: 0;
    background:
      radial-gradient(circle at 22% 30%, var(--olive-glow), transparent 32%),
      radial-gradient(circle at 62% 68%, var(--olive-glow), transparent 30%),
      radial-gradient(circle at 85% 20%, var(--olive-light), transparent 28%),
      linear-gradient(135deg, var(--olive-mid), var(--olive-deep));
  }
  .brand-name {
    font-family: "Cormorant Garamond", serif;
    font-style: italic; font-weight: 500;
    color: var(--paper-text);
    white-space: nowrap;
  }
  .name-band {
    position: absolute; left: 0; top: 186px;
    width: 350px; height: 92px;
    background: var(--ink);
    display: flex; align-items: center; justify-content: flex-end;
    padding-right: 24px;
  }
  .name-band .brand-name { font-size: 34px; }
  .info-panel {
    position: absolute; right: 0; top: 0; bottom: 0;
    width: 262px;
    background: var(--ink);
    display: flex; flex-direction: column; align-items: center;
    padding: 40px 20px 0;
    color: var(--paper-text);
  }
  .info-panel .brand-name { font-size: 25px; }
  .divider {
    width: 150px; height: 1px; background: var(--rule);
    margin: 24px 0;
  }
  .tagline {
    font-family: "Cormorant Garamond", serif;
    font-style: italic; font-weight: 500;
    font-size: 20px; line-height: 1.3;
    text-align: center;
  }
  .contact-list {
    list-style: none; align-self: stretch;
    font-family: "Cormorant Garamond", serif;
    font-style: italic; font-weight: 500;
    font-size: 16px; line-height: 1.6;
    padding-left: 16px;
  }
  .contact-list li { display: flex; align-items: center; gap: 12px; }
  .contact-icon {
    width: 12px; height: 12px; flex: none;
    font-style: normal; font-size: 12px; line-height: 12px;
  }
</style>
</head>
<body>
<main class="canvas">
  <section class="card card--front" aria-label="Card front">
    <div class="pattern-fill" role="img" aria-label="Olive green tone-on-tone floral damask pattern"></div>
    <div class="name-band">
      <span class="brand-name">Liv Harrowby Designs</span>
    </div>
  </section>

  <section class="card card--back" aria-label="Card back">
    <div class="pattern-fill" role="img" aria-label="Olive green tone-on-tone floral damask pattern"></div>
    <div class="info-panel">
      <span class="brand-name">Liv Harrowby Designs</span>
      <div class="divider"></div>
      <p class="tagline">Colour consultancy and<br>interior styling</p>
      <div class="divider"></div>
      <ul class="contact-list">
        <li>
          <svg class="contact-icon" viewBox="0 0 12 12" aria-hidden="true">
            <path d="M3 1 L5 3.5 L4 5 Q5 7 7 8 L8.5 7 L11 9 L9.5 11 Q4 10.5 1 3 Z" fill="none" stroke="#f2f0ea" stroke-width="1"/>
          </svg>
          0417 238 605
        </li>
        <li>
          <span class="contact-icon" aria-hidden="true">@</span>
          livharrowby@qoralnet.net.au
        </li>
      </ul>
    </div>
  </section>
</main>
</body>
</html>
```